Diverse, up-scale salon needs eye-catching, unique business cards.

We are looking for a unique business card design for our stylist but that can also be multi functional and used for appointment reminder and referrals. I will need a design in a format that I can modify names and titles going forward. In the past we have had a dark background with the logo on one side, and stylist and contact information on the other but we are open to all ideas. I have included our mission statement as well as branded colors below. The statement doesn't need to go on the card, it's just a reference for target market. We need space for the stylists name, title, instagram handle and then the salons phone number, website and address. I am also open to adding a spot for a qr code linked to the stylist instagram or the salon booking link.

primary brand colors:
#333333 #233415 #36502a #93874a #000000
Mission statement:
Vessolin Hair Studio, a high-end salon located in the lively Downtown Farmington, Michigan, is committed to providing exceptional services in a welcoming and relaxed environment to meet the needs of our diverse clientele.
Our salon specializes in contemporary custom haircuts, coloring, extensions, and barbering and beard grooming services. Our team of skilled stylists is passionate and inventive in their hair styling techniques. At the heart of our salon are values centered on quality, innovation, creativity, and above all, comfort. These core values are evident in every appointment across our customizable array of services.
Our goal is to establish a benchmark for exceptional hair care for every human.
Website: www.vessolinhairstudio.example
instagram: @vessolinhairstudio
address: 41782 Pelham Crest Rd, Halverton OH
phone: 555-613-4087

Industry/Entity Type

Hair Salon

Contact Information for Business Card

Stylist name, title, phone, instagram, website, address, (optional qr code)

Requirements
Should not have
• Does not need mission statement on the card.

```html
<!DOCTYPE html>
<html lang="en">
<head>
<meta charset="utf-8">
<title>Vessolin Hair Studio — Business Cards</title>
<link rel="stylesheet" href="https://fonts.googleapis.com/css2?family=Montserrat:wght@400;500;600&family=Allura&display=swap">
<style>
  :root {
    --page: #161616;
    --card: #262626;
    --gold: #93874a;
    --ink-light: #d9d9d9;
    --ink-soft: #bdbdbd;
  }
  * { box-sizing: border-box; margin: 0; padding: 0; }
  html, body { width: 1200px; height: 939px; overflow: hidden; }
  body {
    background: var(--page);
    font-family: "Montserrat", Arial, sans-serif;
    position: relative;
  }
  .card {
    position: absolute;
    width: 560px;
    height: 320px;
    background: var(--card);
    border-radius: 16px;
    box-shadow: 0 14px 30px rgba(0,0,0,.55);
  }
  .card__frame {
    position: absolute;
    inset: 12px;
    border: 1px solid var(--gold);
    border-radius: 10px;
  }
  .card--front { left: 150px; top: 100px; }
  .card--back  { left: 490px; top: 500px; }

  /* front */
  .brand-seal {
    position: absolute;
    left: 50%; top: 50%;
    transform: translate(-50%, -50%);
    display: flex;
    flex-direction: column;
    align-items: center;
    gap: 14px;
  }
  .brand-seal__ring {
    width: 92px; height: 92px;
    border: 3px solid var(--gold);
    border-radius: 50%;
  }
  .brand-name {
    color: var(--gold);
    font-weight: 600;
    letter-spacing: 3px;
    text-transform: uppercase;
    font-size: 17px;
    white-space: nowrap;
  }

  /* back */
  .brand-block {
    position: absolute;
    left: 40px; top: 110px;
    width: 220px;
    text-align: center;
  }
  .brand-block .brand-name { font-size: 19px; line-height: 1.5; white-space: normal; }

  .stylist {
    position: absolute;
    left: 285px; top: 50px;
    width: 250px;
  }
  .stylist__name {
    font-family: "Allura", cursive;
    font-size: 38px;
    color: var(--ink-light);
    line-height: 1.1;
    white-space: nowrap;
  }
  .stylist__title {
    font-size: 12px;
    color: var(--ink-soft);
    margin-top: 4px;
  }
  .stylist__rule {
    width: 28px; height: 2px;
    background: var(--gold);
    margin: 12px 0 10px;
  }
  .contact-list { list-style: none; }
  .contact-list li {
    font-size: 12px;
    color: var(--ink-soft);
    line-height: 1.6;
    white-space: nowrap;
  }
  .address {
    position: absolute;
    left: 0; right: 0; bottom: 6px;
    text-align: center;
  }
  .address span {
    background: var(--card);
    padding: 0 10px;
    font-size: 9.5px;
    letter-spacing: 2px;
    color: var(--ink-soft);
    text-transform: uppercase;
  }
</style>
</head>
<body>

  <section class="card card--front" aria-label="Card front">
    <div class="card__frame"></div>
    <div class="brand-seal">
      <div class="brand-seal__ring"></div>
      <div class="brand-name">Vessolin Hair Studio</div>
    </div>
  </section>

  <section class="card card--back" aria-label="Card back">
    <div class="card__frame"></div>
    <div class="brand-block">
      <div class="brand-name">Vessolin<br>Hair Studio</div>
    </div>
    <div class="stylist">
      <div class="stylist__name">Marcus Delray</div>
      <div class="stylist__title">Owner / Hair Stylist</div>
      <div class="stylist__rule"></div>
      <ul class="contact-list">
        <li>555-613-4087</li>
        <li>hello@vessolinhairstudio.example</li>
        <li>www.vessolinhairstudio.example</li>
        <li>@vessolinhairstudio</li>
      </ul>
    </div>
    <div class="address"><span>41782 Pelham Crest Rd, Halverton OH</span></div>
  </section>

</body>
</html>
```